Stage Design Company Business Card

We are looking to step up up our business card design for our team.

We are a Full service Design and Consultation company for Stage and TV with an emphasis in Theatrical Lighting.

We like our materials to be clean and modern with solid colors free of patterns and gradients. Our brand consists of 4 primary colors Purple, Black, Grey, and White. Provided is our Word Mark as well as our Symbol Logo.

We would like our cards to leave an impression beyond the information, show our attention to design and detail, and make our marks an easily recognized feature (together or apart) for our clients.

We need a warm approachable comfortable feel for some clients, and a professional flair for the board member type clients.

Attached are our brand elements, and our existing cards to give a sense of our style and a glipse at the information we provide on our cards.

Target Market(s)

broad client base from church leaders to high school teachers and architects.

Industry/Entity Type

Business

Contact Information for Business Card

We format our phone number with periods not parenthesis or dashes. Information will be edited for each of our team members, and team member specific cards are not part of this scope, but rather a template so to speak.

Font styles to use
Sans Serif

Colors
6b449b
ffffff
000000
333333
aaaaaa

Requirements
Must have
• Wordmark and logo mark present (does not need to exist on the same side of card)
• Brand Colors,
• Name, Phone, Email, Address.
• Unique choices that make someone stop and take a second look
Nice to have
• It would be nice to somehow convey what we DO, as our brand name does not lend itself to this, outside of an obvious tagline though.....
• social media if not crowded. all of our handles match (instagram, twitter, facebook)
Should not have
• "clipart"

```html
<!DOCTYPE html>
<html lang="en">
<head>
<meta charset="utf-8">
<title>Orrin Entertainment – Business Card</title>
<link rel="stylesheet" href="https://fonts.googleapis.com/css2?family=Jura:wght@500;600&display=swap">
<style>
  :root {
    --stage: #161616;
    --card-dark: #111820;
    --card-light: #ffffff;
    --brand-purple: #3b2870;
    --brand-grey: #c4c6c8;
    --ink: #111111;
  }
  * { box-sizing: border-box; margin: 0; padding: 0; }
  html, body {
    width: 1200px;
    height: 1076px;
    overflow: hidden;
    background: var(--stage);
    font-family: "Jura", sans-serif;
  }
  .canvas {
    position: relative;
    width: 1200px;
    height: 1076px;
  }
  .card {
    position: absolute;
    width: 760px;
    height: 438px;
  }
  .card--back {
    left: 110px;
    top: 70px;
    background: var(--card-dark);
    display: flex;
    flex-direction: column;
    align-items: center;
    justify-content: center;
  }
  .brand-dot {
    width: 120px;
    height: 120px;
    border-radius: 50%;
    background: var(--brand-grey);
    margin-bottom: 46px;
  }
  .brand-name {
    color: var(--brand-grey);
    font-weight: 600;
    text-align: center;
    line-height: 1;
  }
  .brand-name__main {
    display: block;
    font-size: 40px;
    letter-spacing: 22px;
    margin-right: -22px;
  }
  .brand-name__sub {
    display: block;
    font-size: 11px;
    letter-spacing: 11px;
    margin-top: 26px;
    margin-right: -11px;
  }
  .card--front {
    left: 330px;
    top: 568px;
    background: var(--card-light);
    overflow: hidden;
  }
  .front-mark {
    position: absolute;
    left: 40px;
    top: 50%;
    transform: translateY(-50%);
    display: flex;
    align-items: center;
    gap: 16px;
  }
  .front-mark__dot {
    width: 34px;
    height: 34px;
    border-radius: 50%;
    background: var(--brand-purple);
  }
  .front-mark__name {
    color: var(--brand-purple);
    font-weight: 600;
    font-size: 40px;
    letter-spacing: 8px;
  }
  .contact {
    position: absolute;
    left: 405px;
    top: 78px;
    width: 296px;
    text-align: center;
    color: var(--ink);
    font-weight: 500;
  }
  .contact__name {
    font-size: 33px;
    letter-spacing: 1px;
    text-transform: uppercase;
    padding-bottom: 14px;
  }
  .contact__rule {
    border: none;
    border-top: 2px dotted var(--brand-purple);
    width: 296px;
  }
  .contact__phone {
    font-size: 30px;
    margin-top: 26px;
  }
  .contact__email {
    font-size: 22px;
    margin-top: 22px;
    margin-bottom: 14px;
  }
  .contact__address {
    font-size: 24px;
    letter-spacing: 2px;
    text-transform: uppercase;
    line-height: 1.45;
    margin-top: 18px;
  }
</style>
</head>
<body>
  <main class="canvas">
    <section class="card card--back" aria-label="Card back">
      <div class="brand-dot"></div>
      <p class="brand-name">
        <span class="brand-name__main">ORRIN</span>
        <span class="brand-name__sub">ENTERTAINMENT</span>
      </p>
    </section>

    <section class="card card--front" aria-label="Card front">
      <div class="front-mark">
        <span class="front-mark__dot"></span>
        <span class="front-mark__name">ORRIN</span>
      </div>
      <div class="contact">
        <p class="contact__name">Mara L Quinlan</p>
        <hr class="contact__rule">
        <p class="contact__phone">555.014.2290</p>
        <p class="contact__email">mara@orrin-e.com</p>
        <hr class="contact__rule">
        <p class="contact__address">18 N Harbor Ave<br>Tolland, OR 97001</p>
      </div>
    </section>
  </main>
</body>
</html>
```